Doctor to Patient Management Website

I need a design for a health management website that connects doctors to patients. The website will consist of: A main page mainly describing our goal, services, and initiatives towards (Who we are AKA "About Us", Our services, Contact Us, Quick Links for health tips, Language selection, Find a doctor, search bar, Member Login Section, small glossary section below with links to all entities mentioned prior, Help section (Helpful tips and tutorials, Used to request help from admin, customer service, to resolve issues or get assistance). A profile page with two types:1) Doctor Profile: Doctor Personal info (First, Last, Middle Name, Title), Clinic, Hospital Info, Department, Credentials, Years of Experience, Patients rating, #Patients seen during the current week, #Patients seen in total, Picture, Link to email doctor, Link to print doctor's profile). Tabs for "About Me", "Contact Info", "Ratings & Comments", "Documents" (To be downloaded and uploaded by patient), "Patients (List of Patients alphabetical order by name)", "Calendar" (to see doctor's availability for booking) underneath all links. 2) Patient profile: About me, Personal Info, Height, Weight, Blood Type, Age, DOB, Name, etc..., Message and email link.Picture of patient with menu made of "Personal Data", "Biometrics", "Allergies", "Illnesses", "Medications", "Medical Procedures", "Doctors" treating the patient, "Documents" (To be downloaded and uploaded by patient). Underneath all, other patients he or she is related to (For example: family member, so patient can't connect to other patients who are family members)3) Login section: New Users will have option to register using:First Name (Required), Last Name, Middle (not required), Address (Not required), City (Required), Country (Required), Email (Not required), Phone Number (Required), Choose UserName, Password, Account Type (Doctor or Patient). Once registered, they will log in using UserName, Password, and Account_Type.Curent Users will log in using UserName, Password, and Account_Type and option to retrieve username or password.Pages to include (Login Page - Registration Page - Retrieve Username and Reset Password Page)Please see link below:https://plumcrate-adwerks.net/importance-claiming-vantorix-quibble-zarn/Pictures are attached to this project as an inspirationFYI: Dummy text can be used to fill in the business, services, and descriptive information. Feel free to include your own ideas in the layout, design, categories, patterns, and more to and showcase your talent. Design and pictures provided are available as source of ideas.

Target Market(s)

Age: 21+ / Family Oriented / Medical Sector / Metropolitan Area / Educated and non Educated Users

Industry/Entity Type

Health Care

Number of Pages Required

5+ page

Font styles to use
Sans Serif

Colors

Designer to choose colors to be used in the design.

Requirements
Must have
• Thin layer design
• Simple font - No serif
• Clean menu with light but solid colors (No Gradient effect)
Nice to have
• Different color themes (2 or 3) can be combined
• Sample pictures for illustration (either as an ad or to go with the flow of your design)
• Dashboard Feel (Suggested but not required)
Should not have
• Artistic fonts - with Serif
• Dark color themes

```html
<!DOCTYPE html>
<html lang="en">
<head>
<meta charset="utf-8">
<title>Medvora – Doctor Profile</title>
<link rel="stylesheet" href="https://fonts.googleapis.com/css2?family=Open+Sans:wght@400;600;700&display=swap">
<style>
:root{
  --ink:#3d3f44;
  --muted:#7b7f86;
  --soft:#a4a8ad;
  --line:#e3e5e8;
  --page:#f1f2f4;
  --white:#ffffff;
  --orange:#f0893a;
  --blue:#58a8d9;
  --blue-pale:#dcecf6;
  --rose:#f6dbd6;
  --rose-ink:#d8674f;
  --footer:#eceef0;
}
*{box-sizing:border-box;margin:0;padding:0}
html,body{width:788px;height:1200px;overflow:hidden}
body{font-family:"Open Sans",Arial,sans-serif;color:var(--ink);background:var(--white);font-size:10px}
.wrap{width:565px;margin:0 auto;position:relative}

.topbar{height:20px}
.topbar .wrap{display:flex;justify-content:space-between;align-items:flex-start}
.lang{font-size:8px;color:var(--muted);padding-top:5px}
.lang b{color:var(--ink);font-weight:600}
.top-actions{display:flex;gap:2px;margin-right:-40px}
.top-actions a{font-size:8px;text-decoration:none;padding:4px 10px;border-radius:0 0 3px 3px}
.btn-login{background:var(--rose);color:var(--rose-ink)}
.btn-find{background:var(--blue-pale);color:#3a86b8}

.header{height:52px;border-bottom:1px solid var(--line)}
.header .wrap{display:flex;justify-content:space-between;align-items:center;height:52px}
.brand{font-size:22px;font-weight:700;color:var(--ink);letter-spacing:-.5px}
.nav{display:flex;gap:18px;list-style:none}
.nav a{font-size:9px;color:var(--ink);text-decoration:none}

.main{background:var(--page);padding:10px 0 30px}
.profile{background:var(--white);display:flex;height:392px}
.photo{width:243px;height:392px;background:linear-gradient(160deg,#f4f6f8 0%,#dfe6ec 45%,#c9d5df 100%)}
.info{flex:1;padding:22px 20px 0 16px}
.info h1{font-size:14px;font-weight:600;color:var(--orange);margin-bottom:12px}
.fields{display:grid;grid-template-columns:92px 10px 1fr;row-gap:0}
.fields dt,.fields dd,.fields span{font-size:9px;line-height:19px;border-bottom:1px solid var(--line)}
.fields dt{font-weight:600}
.fields span{color:var(--muted)}
.fields dd{color:var(--muted)}
.actions{display:flex;gap:6px;margin:20px 0 0 92px}
.actions a{font-size:7.5px;font-weight:600;color:#fff;text-decoration:none;padding:5px 14px;text-transform:uppercase}
.send{background:var(--orange)}
.print{background:var(--blue)}
.stats{display:flex;margin-top:22px;border-top:1px solid var(--line)}
.stat{padding:10px 12px 0 0;border-right:1px solid var(--line);margin-right:12px;width:92px}
.stat:last-child{border-right:0}
.stat.rating{width:100px}
.stat-label{font-size:8px;font-weight:600;margin-bottom:3px}
.stars{display:flex;gap:1px}
.stat small{display:block;font-size:7.5px;color:var(--muted);margin-top:3px;line-height:10px}
.stat strong{font-size:22px;font-weight:400;color:var(--blue);display:block;line-height:26px}

.tabs{display:flex;gap:2px;margin-top:30px;list-style:none}
.tabs li{font-size:9px;padding:7px 14px;background:var(--blue-pale);color:#3a86b8}
.tabs li.active{background:var(--rose);color:var(--rose-ink);font-weight:600}
.tab-panel{background:var(--white);padding:18px 16px 10px;height:372px}
.tab-panel h2{font-size:13px;font-weight:600;margin-bottom:10px}
.tab-panel p{font-size:7.5px;line-height:12.5px;color:var(--muted);margin-bottom:8px}
.tab-panel h2+p{margin-top:0}
.tab-panel p+h2{margin-top:18px}

.footer{background:var(--footer);height:282px;padding-top:28px;position:relative}
.cols{display:grid;grid-template-columns:repeat(4,1fr);gap:20px}
.col h3{font-size:10px;font-weight:600;margin-bottom:6px;display:flex;align-items:center;gap:5px}
.col h3.sub{margin-top:12px}
.col ul{list-style:none}
.col li,.col address{font-size:7.5px;line-height:13px;color:var(--muted);font-style:normal}
.bottom{position:absolute;left:0;right:0;bottom:10px}
.bottom .wrap{display:flex;justify-content:space-between;border-top:1px solid #d8dbde;padding-top:8px;font-size:7.5px;color:var(--muted)}
.bottom .legal{display:flex;gap:14px}
</style>
</head>
<body>
<div class="topbar"><div class="wrap">
  <div class="lang">Language: <b>English</b> ▾</div>
  <div class="top-actions"><a class="btn-login" href="#">Member Login</a><a class="btn-find" href="#">Find a Doctor</a></div>
</div></div>

<header class="header"><div class="wrap">
  <div class="brand">Medvora</div>
  <ul class="nav"><li><a href="#">Home</a></li><li><a href="#">About</a></li><li><a href="#">Patients</a></li><li><a href="#">Reviews</a></li><li><a href="#">FAQ</a></li><li><a href="#">Contact Us</a></li></ul>
</div></header>

<main class="main"><div class="wrap">
  <section class="profile">
    <div class="photo" role="img" aria-label="Portrait photo of the doctor in a white coat with a stethoscope"></div>
    <div class="info">
      <h1>Doctor Personal info</h1>
      <dl class="fields">
        <dt>First Name</dt><span>:</span><dd>Lorems</dd>
        <dt>Last Name</dt><span>:</span><dd>Dummy Kafaet</dd>
        <dt>Middle Name</dt><span>:</span><dd>Julian</dd>
        <dt>Title</dt><span>:</span><dd>Lorem ipsum dolor sit am</dd>
        <dt>Clinic</dt><span>:</span><dd>Lorem ipsum dolor sit am</dd>
        <dt>Hospital Info</dt><span>:</span><dd>Dummy Lorem</dd>
        <dt>Department</dt><span>:</span><dd>Medicine</dd>
        <dt>Credentials</dt><span>:</span><dd>Associate Professor</dd>
        <dt>Years of Experience</dt><span>:</span><dd>7 Years</dd>
      </dl>
      <div class="actions"><a class="send" href="#">Send Message</a><a class="print" href="#">Print Doctor's Profile</a></div>
      <div class="stats">
        <div class="stat rating">
          <div class="stat-label">Patients Rating</div>
          <div class="stars">
            <svg width="60" height="11" viewBox="0 0 60 11" aria-hidden="true">
              <g fill="#f0893a">
                <polygon points="5.5,0 7,3.8 11,4 8,6.6 9,10.5 5.5,8.4 2,10.5 3,6.6 0,4 4,3.8"/>
                <polygon transform="translate(12,0)" points="5.5,0 7,3.8 11,4 8,6.6 9,10.5 5.5,8.4 2,10.5 3,6.6 0,4 4,3.8"/>
                <polygon transform="translate(24,0)" points="5.5,0 7,3.8 11,4 8,6.6 9,10.5 5.5,8.4 2,10.5 3,6.6 0,4 4,3.8"/>
                <polygon transform="translate(36,0)" points="5.5,0 7,3.8 11,4 8,6.6 9,10.5 5.5,8.4 2,10.5 3,6.6 0,4 4,3.8"/>
              </g>
              <polygon transform="translate(48,0)" fill="#d9dcdf" points="5.5,0 7,3.8 11,4 8,6.6 9,10.5 5.5,8.4 2,10.5 3,6.6 0,4 4,3.8"/>
            </svg>
          </div>
          <small>4.0 out of Stars</small>
        </div>
        <div class="stat"><strong>62</strong><small>Patients seen during the current week</small></div>
        <div class="stat"><strong>525</strong><small>Patients seen in total</small></div>
      </div>
    </div>
  </section>

  <ul class="tabs"><li class="active">About Me</li><li>Contact Info</li><li>Ratings &amp; Comments</li><li>Documents</li><li>Patients</li><li>Calendar</li></ul>
  <section class="tab-panel">
    <h2>Sed ut perspiciatimmis iste natus accusa</h2>
    <p>Sed ut perspiciatis unde omnis iste natus error sit voluptatem accusantium doloremque laudantium, totam rem aperiam, eaque ipsa quae ab illo inventore veritatis et quasi architecto beatae vitae dicta sunt explicabo. Nemo enim ipsam voluptatem quia voluptas sit aspernatur aut odit aut fugit, sed quia consequuntur magni dolores eos qui ratione voluptatem sequi nesciunt. Neque porro quisquam est, qui dolorem ipsum quia dolor sit amet, consectetur, adipisci velit, sed quia non numquam eius modi tempora incidunt ut labore et dolore magnam aliquam quaerat voluptatem.</p>
    <p>Sed ut perspiciatis unde omnis iste natus error sit voluptatem accusantium doloremque laudantium, totam rem aperiam, eaque ipsa quae ab illo inventore veritatis et quasi architecto beatae vitae dicta sunt explicabo. Nemo enim ipsam voluptatem quia voluptas sit aspernatur aut odit aut fugit, sed quia consequuntur magni dolores eos qui ratione voluptatem sequi nesciunt.</p>
    <h2>Sed ut perspiciatimmis iste natus accusa</h2>
    <p>Sed ut perspiciatis unde omnis iste natus error sit voluptatem accusantium doloremque laudantium, totam rem aperiam, eaque ipsa quae ab illo inventore veritatis et quasi architecto beatae vitae dicta sunt explicabo. Nemo enim ipsam voluptatem quia voluptas sit aspernatur aut odit aut fugit, sed quia consequuntur magni dolores eos qui ratione voluptatem sequi nesciunt. Neque porro quisquam est, qui dolorem ipsum quia dolor sit amet, consectetur, adipisci velit, sed quia non numquam eius modi tempora incidunt ut labore et dolore magnam aliquam quaerat voluptatem.</p>
    <p>Sed ut perspiciatis unde omnis iste natus error sit voluptatem accusantium doloremque laudantium, totam rem aperiam, eaque ipsa quae ab illo inventore veritatis et quasi architecto beatae vitae dicta sunt explicabo.</p>
  </section>
</div></main>

<footer class="footer">
  <div class="wrap cols">
    <div class="col">
      <h3><svg width="9" height="11" viewBox="0 0 9 11" aria-hidden="true"><path d="M4.5 0A4.2 4.2 0 0 0 .3 4.2C.3 7.3 4.5 11 4.5 11S8.7 7.3 8.7 4.2A4.2 4.2 0 0 0 4.5 0z" fill="#7b7f86"/><circle cx="4.5" cy="4.2" r="1.5" fill="#eceef0"/></svg>Contact Us</h3>
      <address>Medvora<br>Lorem Ipsum Dolor<br>Harlow Street 14<br>0000 Lorem</address>
      <h3 class="sub"><svg width="11" height="8" viewBox="0 0 11 8" aria-hidden="true"><rect x=".5" y=".5" width="10" height="7" fill="none" stroke="#7b7f86"/><path d="M.5 .5l5 4 5-4" fill="none" stroke="#7b7f86"/></svg>Email</h3>
      <address>info@medvora.example</address>
      <h3 class="sub"><svg width="9" height="11" viewBox="0 0 9 11" aria-hidden="true"><rect x=".5" y=".5" width="8" height="10" rx="1.5" fill="none" stroke="#7b7f86"/><circle cx="4.5" cy="8.5" r=".8" fill="#7b7f86"/></svg>Phone</h3>
      <address>(000) 555-0100</address>
    </div>
    <div class="col">
      <h3>Patient Resources</h3>
      <ul><li>Lorem ipsum dolor</li><li>Consectetur adipiscin</li><li>Sed ut perspiciatis</li></ul>
      <h3 class="sub">General Information</h3>
      <ul><li>Lorem ipsum dolor</li><li>Consectetur adipiscin</li><li>Sed ut perspiciatis</li></ul>
    </div>
    <div class="col">
      <h3>Quick Links</h3>
      <ul><li>In alia ictus sint</li><li>Sed ut perspiciatis</li><li>Nemo enim ipsam alte</li><li>Perspiciatis unde</li><li>Omnis iste natus err</li><li>In alia ictus sint</li></ul>
    </div>
    <div class="col">
      <h3>Glossary</h3>
      <ul><li>Sed ut perspiciatis unt</li><li>Sedatim accusantium</li><li>Nemo enim ipsam vol</li><li>Sed ut perspiciatis unt</li><li>Quia volup tem alias</li><li>Doloremque lauda</li></ul>
    </div>
  </div>
  <div class="bottom"><div class="wrap">
    <span>© 2015 Medvora. All rights reserved</span>
    <span class="legal"><span>Terms of Use</span><span>Privacy Policy</span></span>
  </div></div>
</footer>
</body>
</html>
```